13 Varno - new website design project

Our company Varno Electrical is developing a new lead generation website focused on Electrical, LED Lighting and Solar Power. We need a high converting website.

Example of our current website is www.varnoelectrical-example.com.au You can take content from this website for this new design. Our colours are red, black and white. For our new website we would like to promote Varno, Spark Every Day. Please listen to the jingle.

The below link is the company jingle that we have developed.
http://www.tunecraftdemo.com.au/vrn-tc-v1/

The key for this brief is to generate leads for Electrical, LED Lighting (for commercial) and Solar Power & Storage.

Target Market(s)

Business owners in Melbourne Victoria

Number of Pages Required

4 page

Colors
ec1f27
ffffff

Requirements
Must have
• This page must be clean, be in line with company branding and a high converting lead website.

```html
<!DOCTYPE html>
<html lang="en">
<head>
<meta charset="utf-8">
<title>Varno Electrical — Home</title>
<link rel="stylesheet" href="https://fonts.googleapis.com/css2?family=Roboto:wght@400;500;700&display=swap">
<style>
:root{
  --red:#ec1f27;
  --dark:#30323a;
  --darker:#2a2b31;
  --ink:#222;
  --body:#444;
  --light:#f4f4f4;
  --white:#fff;
  --line:#d9d9d9;
}
*{box-sizing:border-box;margin:0;padding:0}
html,body{width:1200px;height:3087px;overflow:hidden}
body{font-family:"Roboto",Arial,sans-serif;color:var(--ink);background:var(--white);position:relative}

/* hero */
.hero{position:absolute;left:0;top:0;width:1200px;height:603px;overflow:hidden}
.hero-photo{position:absolute;inset:0;background:linear-gradient(100deg,#e6e8eb 0%,#d3d6db 35%,#7d8394 58%,#c9ccd2 78%,#eceef0 100%)}
.sidebar{position:absolute;left:99px;top:0;width:239px;height:603px;background:var(--white);box-shadow:0 0 12px rgba(0,0,0,.12)}
.brand{position:absolute;left:24px;top:30px;display:flex;align-items:center;gap:10px}
.brand-dot{width:34px;height:34px;border-radius:50%;background:var(--red)}
.brand-name{font-size:40px;font-weight:700;color:var(--red);line-height:1}
.brand-tag{position:absolute;left:68px;top:78px;font-size:15px;color:var(--ink)}
.nav{list-style:none;position:absolute;left:0;top:142px;width:239px}
.nav li{height:62px;line-height:62px;text-align:center;font-size:13px;color:#333}
.nav li.active{background:var(--red);color:var(--white);height:41px;line-height:41px}
.slider-arrows{position:absolute;left:1036px;top:492px}
.callbar{position:absolute;left:761px;top:552px;width:439px;height:51px;background:var(--red);clip-path:polygon(26px 0,100% 0,100% 100%,0 100%)}
.callbar .ico{position:absolute;left:52px;top:7px;width:38px;height:38px;border-radius:50%;background:var(--white)}
.callbar span{position:absolute;left:108px;top:13px;color:var(--white);font-size:22px}

/* about */
.about{position:absolute;left:0;top:603px;width:1200px;height:276px;background:var(--red);color:var(--white);text-align:center}
.about h2{margin-top:50px;font-size:25px;font-weight:500}
.about p{width:900px;margin:24px auto 0;font-size:16.5px;line-height:31px}
.readmore{position:absolute;left:520px;top:237px;width:160px;height:39px;background:var(--dark);clip-path:polygon(22px 0,100% 0,calc(100% - 22px) 100%,0 100%);color:var(--white);font-size:15px;line-height:39px}
.readmore b{font-weight:700}

/* services */
.services{position:absolute;left:0;top:879px;width:1200px;height:370px;background:var(--dark)}
.svc-title{position:absolute;top:57px;width:300px;text-align:center;color:var(--white);font-size:15px}
.card{position:absolute;top:107px;width:300px;height:189px}
.card-face{position:absolute;inset:0;clip-path:polygon(30px 0,100% 0,calc(100% - 30px) 100%,0 100%);background:var(--white)}
.card-text{position:absolute;left:52px;top:30px;width:196px;font-size:11px;line-height:17px;color:#555;text-align:center}
.card-text em{display:block;font-style:normal;color:var(--red);font-weight:500;margin-top:6px}
.card-badge{position:absolute;right:6px;bottom:-10px;width:46px;height:46px;border-radius:50%;background:var(--white);box-shadow:0 2px 6px rgba(0,0,0,.3);display:flex;align-items:center;justify-content:center}

/* why */
.why-title{position:absolute;left:0;top:1295px;width:1200px;text-align:center;font-size:25px;font-weight:500}
.num{position:absolute;width:97px;height:96px;border:2px solid var(--line);box-shadow:0 0 0 4px #f2f2f2;font-size:36px;font-weight:500;display:flex;align-items:center;justify-content:center}
.why-item{position:absolute}
.why-item h3{font-size:16px;font-weight:500;margin-bottom:14px}
.why-item p{font-size:13px;line-height:24px;color:var(--body)}

/* clients */
.clients{position:absolute;left:0;top:2099px;width:1200px;height:344px;background:var(--light)}
.clients h2{position:absolute;top:35px;width:100%;text-align:center;font-size:25px;font-weight:500}
.client{position:absolute;top:126px;width:230px;height:127px;border:5px solid var(--white);box-shadow:0 2px 6px rgba(0,0,0,.15);display:flex;align-items:center;justify-content:center;text-align:center;font-weight:700;font-size:24px;line-height:28px}
.dots{position:absolute;top:296px;left:566px;display:flex;gap:8px}
.dots i{width:10px;height:10px;border-radius:50%;background:#c8c8c8}

/* testimonial */
.testi-photo{position:absolute;left:181px;top:2506px;width:194px;height:194px;border-radius:50%;border:6px solid var(--white);box-shadow:0 2px 10px rgba(0,0,0,.25);background:linear-gradient(180deg,#ececec,#9aa2ad 60%,#6c7480)}
.quote-badge{position:absolute;left:335px;top:2526px;width:46px;height:46px;border-radius:50%;background:var(--red);color:var(--white);font-size:40px;font-weight:700;text-align:center;line-height:58px}
.testi{position:absolute;left:420px;top:2500px;width:520px;text-align:center}
.testi h2{font-size:25px;font-weight:500}
.testi p{margin-top:18px;font-size:14px;line-height:33px;color:#333}
.testi .who{margin-top:4px;font-size:19px;font-weight:700}

/* footer */
.footer{position:absolute;left:0;top:2758px;width:1200px;height:296px;background:var(--red);color:var(--white)}
.fcol{position:absolute;top:33px}
.fcol h4{font-size:19px;font-weight:500;margin-bottom:24px}
.fcol ul{list-style:none}
.fcol li{font-size:13px;height:31px}
.fcol li::before{content:"›";margin-right:14px;font-size:16px}
.field{position:absolute;left:611px;width:194px;background:var(--white);font-size:10px;color:#777;padding:8px 8px}
.submit{position:absolute;left:611px;top:203px;width:74px;height:23px;background:var(--dark);color:var(--white);font-size:12px;text-align:center;line-height:23px}
.fcall{position:absolute;left:617px;top:240px;font-size:13px}
.fcall b{font-size:22px;font-weight:400;margin-left:4px}
.social{position:absolute;top:90px;width:30px;height:30px;background:var(--white)}
.social.dark{background:#a8151b}
.likes{position:absolute;left:400px;top:154px;display:flex;gap:6px}
.likes i{width:58px;height:16px;background:#3b5a9a;border-radius:2px}
.fbrand{position:absolute;left:905px;top:172px}
.fbrand .n{font-size:54px;font-weight:700;line-height:1}
.fbrand .t{font-size:16px;margin-left:26px}
.copy{position:absolute;left:0;top:3054px;width:1200px;height:33px;background:var(--darker);color:#ddd;font-size:12px;text-align:center;line-height:33px}
</style>
</head>
<body>

<header class="hero">
  <div class="hero-photo" role="img" aria-label="Photo of a smiling electrician in hard hat holding a coil of cable, soft grey office background"></div>
  <nav class="sidebar">
    <div class="brand"><span class="brand-dot"></span><span class="brand-name">VARNO</span></div>
    <div class="brand-tag">Spark Every Day</div>
    <ul class="nav">
      <li class="active">HOME</li>
      <li>VARNO STORY</li>
      <li>OUR WORK</li>
      <li>CONTACT US</li>
      <li>ELECTRICAL</li>
      <li>LED LIGHTING</li>
      <li>SOLAR POWER</li>
    </ul>
  </nav>
  <svg class="slider-arrows" width="40" height="30" viewBox="0 0 40 30" aria-hidden="true">
    <path d="M12 6 L4 15 L12 24 M28 6 L36 15 L28 24" fill="none" stroke="#111" stroke-width="2.5"/>
  </svg>
  <div class="callbar">
    <div class="ico"><svg width="38" height="38" viewBox="0 0 38 38"><path d="M13 11c1-1 2-1 3 0l2 3c.5 1 0 2-1 2.5 1 2 3 4 5 5 .5-1 1.5-1.5 2.5-1l3 2c1 1 1 2 0 3-2 2-5 2-9-1.5S11 16 11 14c0-1 1-2 2-3z" fill="#ec1f27"/></svg></div>
    <span>Call Us : 13 7206 VARNO</span>
  </div>
</header>

<section class="about">
  <h2>ABOUT US</h2>
  <p>Varno Electrical was formed to be an expert Electricity Contracting Company providing services to all Residential and Commercial Customers. With over 10 years of experience, Varno Electrical has developed a highly-experienced team of professionals that ensure all our customer expectations are met.</p>
  <div class="readmore"><b>Read</b> more</div>
</section>

<section class="services">
  <div class="svc-title" style="left:132px">ELECTRICAL</div>
  <div class="svc-title" style="left:449px">LED LIGHTING</div>
  <div class="svc-title" style="left:768px">SOLAR POWER</div>

  <div class="card" style="left:132px">
    <div class="card-face"></div>
    <p class="card-text">Safe wiring, switchboard upgrades and fault finding for offices, shops and warehouses across Melbourne, done right the first time by licensed electricians.<em>Read more</em></p>
    <div class="card-badge"><svg width="24" height="24" viewBox="0 0 24 24"><circle cx="12" cy="12" r="10" fill="none" stroke="#ec1f27" stroke-width="2"/><path d="M9 6v4M15 6v4M7 10h10v3a5 5 0 0 1-10 0zM12 18v3" fill="none" stroke="#ec1f27" stroke-width="2"/></svg></div>
  </div>
  <div class="card" style="left:449px">
    <div class="card-face" role="img" aria-label="Photo of LED light bulbs" style="background:linear-gradient(135deg,#eeeff1,#c4c7cc)"></div>
    <div class="card-badge"><svg width="24" height="24" viewBox="0 0 24 24"><path d="M12 3a6 6 0 0 0-3.5 10.9V17h7v-3.1A6 6 0 0 0 12 3zM9.5 20h5" fill="none" stroke="#ec1f27" stroke-width="2"/></svg></div>
  </div>
  <div class="card" style="left:768px">
    <div class="card-face" role="img" aria-label="Photo of a solar panel array outdoors" style="background:linear-gradient(135deg,#a9c3de,#7f98b4)"></div>
    <div class="card-badge"><svg width="24" height="24" viewBox="0 0 24 24"><path d="M5 5h14l2 10H3zM3 10h18M9 5l-1 10M15 5l1 10M12 15v4M8 19h8" fill="none" stroke="#ec1f27" stroke-width="1.6"/></svg></div>
  </div>
</section>

<h2 class="why-title">WHY CHOOSE US ?</h2>

<div class="num" style="left:191px;top:1406px">01</div>
<div class="why-item" style="left:311px;top:1412px;width:700px">
  <h3>PROFESSIONAL SERVICE</h3>
  <p>When you hire a Varno Electrical Electrician you will get a professional and well-presented Electrician that comes skilled and ready to do the job.</p>
</div>

<div class="num" style="left:911px;top:1548px">02</div>
<div class="why-item" style="left:191px;top:1553px;width:690px">
  <h3>5 YEAR WORKMANSHIP GUARANTEE</h3>
  <p>You can buy with confidence as all of our work has a 5 year workmanship guarantee. For your peace of mind, we unconditionally back our electrical work. We will come back to fix any problems at our own expense.</p>
</div>

<div class="num" style="left:191px;top:1673px">03</div>
<div class="why-item" style="left:311px;top:1679px;width:700px">
  <h3>VALUE FOR MONEY</h3>
  <p>We provide extremely competitive pricing, which means you get value for money on quality that is comparable to the best in the industry.</p>
</div>

<div class="num" style="left:911px;top:1817px">04</div>
<div class="why-item" style="left:191px;top:1822px;width:690px">
  <h3>ENVIRONMENTALLY FRIENDLY</h3>
  <p>We a committed to reducing carbon emissions by installing Solar Power and upgrading sites to LED Lighting. In addition to reducing the carbon emissions we recycle Fluorescent Tubes, Highbay Globes, Metal and Cardboard.</p>
</div>

<div class="num" style="left:191px;top:1941px">05</div>
<div class="why-item" style="left:311px;top:1948px;width:700px">
  <h3>FULLY INSURED</h3>
  <p>Varno Electrical is fully insured and equipped to handle break downs and service call outs.</p>
</div>

<section class="clients">
  <h2>OUR SATISFIED CLIENTS INCLUDE...</h2>
  <div class="client" style="left:99px;background:var(--white);color:var(--red)">Lumaland</div>
  <div class="client" style="left:357px;background:#f5e81c;color:#111">Outback<br>Supply Co</div>
  <div class="client" style="left:614px;background:#d9251f;color:var(--white)">Heron<br>Plumbing Supplies</div>
  <div class="client" style="left:869px;background:#c8101a;color:var(--white)">Goldarch Diner</div>
  <div class="dots"><i></i><i></i><i></i><i></i></div>
</section>

<div class="testi-photo" role="img" aria-label="Photo of a client's retail store interior"></div>
<div class="quote-badge">"</div>
<div class="testi">
  <h2>CLIENT TESTIMONIALS</h2>
  <p>" They clean up after the job, explained everything I needed to know and answered all questions, very professional. Will use them again in the future! "</p>
  <div class="who">R. Delman &nbsp;|&nbsp; Balwyn North VIC</div>
</div>

<footer class="footer">
  <div class="fcol" style="left:136px">
    <h4>Quick Links</h4>
    <ul><li>Led Lighting</li><li>Solar Power</li><li>Electrical</li><li>Career</li></ul>
  </div>
  <div class="fcol" style="left:372px">
    <h4>Others</h4>
    <ul><li>Terms &amp; Conditions</li><li>Privacy</li></ul>
  </div>
  <div class="likes" aria-hidden="true"><i></i><i></i></div>
  <div class="fcol" style="left:611px"><h4>Contact Us</h4></div>
  <div class="field" style="top:74px;height:29px">Name</div>
  <div class="field" style="top:109px;height:27px">Email</div>
  <div class="field" style="top:144px;height:45px">Message</div>
  <div class="submit">Submit</div>
  <div class="fcall">Call Us : <b>13 7206 VARNO</b></div>
  <div class="fcol" style="left:908px"><h4>Follow Us</h4></div>
  <div class="social" style="left:908px"></div>
  <div class="social dark" style="left:952px"></div>
  <div class="social dark" style="left:996px"></div>
  <div class="fbrand"><div class="n">VARNO</div><div class="t">Spark Every Day</div></div>
</footer>
<div class="copy">Copyright © 2017. www.varnoelectrical-example.com.au &nbsp;|&nbsp; All Rights Reserved.</div>

</body>
</html>
```